San Francisco Leading Consulting firm - 47Vora Web Design Project

•Create a Web Design
•Uncoded webpage layout design
•2 Pages Design - Homepage + Interior Page

Task Description
Hello, we're looking for a re-design our current website www.47vora-example.com

we have a sample mockup design @

http://47vora.pubtrellis-example.org/

This shows the layout that we like and also a sample of 6 pictures that would change based on where you mouse over..

6 pictures HOME design needs to be included.

SMART
THOUGHTFUL
FLEXIBLE
CREATIVE SERVICES
TECHNICAL SERVICES
PARTNERS

sites we like:

http://www.melvanadvisory-example.com/Home.cfm?id=Home
http://www.plinthworks-example.com/index.html

Our company can be best described as: 100+ employees, cutting-edge, depandable, innovative, strong, smart.

Our Primary focus is: IT Consulting Services and Creative Design services

47Vora LLC is a consulting firm providing creative design, business and technology solutions to both private and public interests.

Established in 1996, 47Vora is a San Francisco based company providing specialists for a range of business needs including:

Creative Design Services
•Print
•Logo Design
•Website Design
•Illustration

and

Business and Technology solutions

•Application Software and Web Development
•Business Process Re-Design (BPR)
•Business/Systems Analysis and Requirement Documentation
•Mentoring and Training
•Network/Hardware Installation Services
•System Design and Architecture
•Vendor Management
•Docuvault Architecture and Implementation

our sample mockup site:

Reason: Due to holiday season, we're not available to work with designers and finilize our design.  

Thank you very much for submitting your design.

We appreciate your time and creativity.   Since, our office is currently closed for holidays, we will be reviewing it in details next week and will make our decision as soon as possible.

It would be great if you could submit any of your changes by Wed next week, so it would be part of our reviews. 

Please see updated wireframe under attachments:  we have some minor updates to our wireframe that we would like you to update your designs, if possible.  

We also encorouge you not to use our standard wireframe and come up with more unique designs.   Everything would be considered when we review your design.

 

Target Market(s)

Creative services and professional services clients, including government agencies

Industry/Entity Type

Business

Requirements
Must have
• Clean, professional look, easy navigation

```html
<!DOCTYPE html>
<html lang="en">
<head>
<meta charset="utf-8">
<title>47Vora — Technology Solutions</title>
<link rel="stylesheet" href="https://fonts.googleapis.com/css2?family=Montserrat:wght@500;600;700&family=Arimo:wght@400;700&family=Lato:wght@300;400&display=swap">
<style>
:root{
  --page:#ffffff;
  --band:#eef1f4;
  --hero-band:#e4e9ee;
  --ink:#3a3a3a;
  --muted:#6b6b6b;
  --rule:#dcdfe3;
  --cyan:#3cc8ee;
  --cyan-deep:#1fb1dc;
  --orange:#f3a020;
  --magenta:#b8187c;
  --button:#767676;
  --photo-warm:#cfc6bb;
  --photo-cool:#a9c3d8;
}
*{box-sizing:border-box;margin:0;padding:0}
html,body{width:1057px;height:1200px;overflow:hidden;background:var(--page)}
body{position:relative;font-family:"Arimo",Arial,sans-serif;color:var(--ink)}
.abs{position:absolute}

/* header */
.masthead{left:0;top:0;width:1057px;height:100px;background:var(--band)}
.brand{left:127px;top:30px;display:flex;align-items:center;gap:10px;font-family:"Montserrat",sans-serif;font-weight:600;font-size:26px;color:#2f4a6b}
.brand-dot{width:22px;height:22px;border-radius:50%;background:var(--cyan-deep)}
.tagline{left:309px;top:49px;font-size:12px;color:#444}
.search{left:829px;top:55px;width:144px;height:21px;background:#fff;border:1px solid #e0e3e6;font-size:8px;color:#999;padding:6px 8px;letter-spacing:.5px}
.search svg{position:absolute;right:6px;top:4px}

/* intro band */
.intro{left:0;top:100px;width:1057px;height:189px;background:#fff}
.nav{left:127px;top:112px;width:158px;list-style:none}
.nav li{height:34px;border-bottom:1px solid var(--rule);font-family:"Montserrat",sans-serif;font-weight:600;font-size:10.5px;letter-spacing:1px;color:#333;padding-top:9px}
.nav li:last-child{border-bottom:none}
.nav .chev{color:var(--orange);margin-left:6px;font-weight:700}
.intro-divider{left:301px;top:116px;width:1px;height:156px;background:var(--rule)}
.welcome{left:324px;top:116px;font-family:"Lato",sans-serif;font-weight:400;font-size:32px;color:var(--cyan)}
.intro-copy{left:324px;top:163px;width:640px;font-size:11.5px;line-height:22px;color:#444}
.intro-copy p+p{margin-top:11px}

/* hero */
.hero{left:0;top:289px;width:1057px;height:300px;background:var(--hero-band)}
.thumbs{left:172px;top:294px;width:80px}
.thumb{width:80px;height:45px;margin-bottom:3.5px;opacity:.75}
.thumb.active{opacity:1}
.hero-photo{left:280px;top:289px;width:556px;height:300px;background:linear-gradient(160deg,#e8e6e1 0%,#cfc9c0 45%,#8f8c88 100%)}
.hero-side{left:836px;top:289px;width:131px;height:300px;background:linear-gradient(180deg,#dbe8f2,#8eb2cf 60%,#c9dbe8)}
.hero-pointer{left:272px;top:408px}
.hero-caption{left:524px;top:333px;width:443px;height:84px;background:rgba(255,255,255,.85)}
.hero-caption svg{position:absolute;left:14px;top:14px}
.hero-title{position:absolute;left:42px;top:2px;font-family:"Arimo",sans-serif;font-size:46px;color:#111}
.hero-sub{position:absolute;left:45px;top:55px;font-size:19px;color:#111}

/* feature columns */
.feature{top:631px;width:268px;height:286px;border-left:1px solid var(--rule)}
.feature-arrow{position:absolute;left:-1px;top:8px}
.feature-label{position:absolute;left:13px;top:6px;font-family:"Lato",sans-serif;font-size:14px;color:#666}
.feature-title{position:absolute;left:21px;top:41px;font-family:"Montserrat",sans-serif;font-weight:700;font-size:17px;letter-spacing:.5px}
.feature-media{position:absolute;left:21px;top:75px;width:256px;height:82px}
.feature-copy{position:absolute;left:21px;top:170px;width:250px;font-size:11px;line-height:20px;color:#444}
.btn{position:absolute;left:21px;top:249px;width:75px;height:29px;background:var(--button);color:#fff;font-size:12px;border-radius:3px;text-align:center;line-height:29px;box-shadow:2px 2px 3px rgba(0,0,0,.25)}
.t-magenta{color:var(--magenta)}
.t-orange{color:var(--orange)}
.t-cyan{color:var(--cyan-deep)}

/* services footer */
.services{left:80px;top:960px;width:885px;height:193px;background:#fff;box-shadow:0 -8px 14px -8px rgba(0,0,0,.18),0 8px 14px -8px rgba(0,0,0,.18)}
.svc-head{font-family:"Arimo",sans-serif;font-weight:700;font-size:12.5px;color:#444}
.svc-list{list-style:none;font-size:10px;color:#333}
.svc-list li{position:relative;padding-left:8px;margin-bottom:12px;line-height:13px}
.svc-list li::before{content:"";position:absolute;left:0;top:5px;width:3px;height:3px;border-radius:50%;background:#333}
.svc-divider{left:384px;top:982px;width:1px;height:156px;background:var(--rule)}
.copyright{left:0;top:1170px;width:1057px;text-align:center;font-size:10px;color:#333}
</style>
</head>
<body>

<header class="masthead abs"></header>
<div class="brand abs"><span class="brand-dot"></span>47Vora</div>
<div class="tagline abs">Thechnology Solutions for the 21st Century</div>
<div class="search abs">SEARCH
  <svg width="12" height="12" viewBox="0 0 12 12"><circle cx="7" cy="5" r="3.5" fill="none" stroke="#f3a020" stroke-width="1.5"/><line x1="4.5" y1="7.5" x2="1.5" y2="10.5" stroke="#f3a020" stroke-width="1.8"/></svg>
</div>

<section class="intro abs"></section>
<ul class="nav abs">
  <li>COMPANY<span class="chev">›</span></li>
  <li>TECHNICAL SERVICES<span class="chev">›</span></li>
  <li>CREATIVE SERVICES<span class="chev">›</span></li>
  <li>PARTNERS<span class="chev">›</span></li>
  <li>CONTACT US</li>
</ul>
<div class="intro-divider abs"></div>
<h1 class="welcome abs">welcome</h1>
<div class="intro-copy abs">
  <p>47Vora LLC is a consulting firm providing creative design, business and technology solutions to both private and public interests.</p>
  <p>Our experts possess broad industry knowledge which can help with technical and businessprocess challenges, delivering solutions that are creative and cost effective.</p>
</div>

<section class="hero abs"></section>
<div class="thumbs abs">
  <div class="thumb" role="img" aria-label="Thumbnail: hands at work" style="background:linear-gradient(135deg,#d9cfc6,#b8a99d)"></div>
  <div class="thumb" role="img" aria-label="Thumbnail: businessman with documents" style="background:linear-gradient(135deg,#d5d8dc,#a5abb2)"></div>
  <div class="thumb active" role="img" aria-label="Thumbnail: man working on laptop" style="background:linear-gradient(135deg,#e2dfd9,#8f8c88)"></div>
  <div class="thumb" role="img" aria-label="Thumbnail: colourful pencils" style="background:linear-gradient(135deg,#8fb07a,#c27a5a,#6a7fb0)"></div>
  <div class="thumb" role="img" aria-label="Thumbnail: team network graphic" style="background:linear-gradient(135deg,#cfd5dc,#9aa3ad)"></div>
  <div class="thumb" role="img" aria-label="Thumbnail: handshake" style="background:linear-gradient(135deg,#e6e2dc,#b9b1a6)"></div>
</div>
<div class="hero-photo abs" role="img" aria-label="Photo: young professional working on a laptop in a bright office lobby"></div>
<div class="hero-side abs" role="img" aria-label="Photo: flexible blue metallic spiral"></div>
<svg class="hero-pointer abs" width="9" height="16" viewBox="0 0 9 16"><polygon points="9,0 0,8 9,16" fill="#4a5560"/></svg>
<div class="hero-caption abs">
  <svg width="14" height="26" viewBox="0 0 14 26"><polyline points="2,2 12,13 2,24" fill="none" stroke="#3cc8ee" stroke-width="4"/></svg>
  <div class="hero-title">flexible</div>
  <div class="hero-sub">the world moves too fast for rigid solutions</div>
</div>

<section class="feature abs" style="left:121px">
  <svg class="feature-arrow" width="6" height="12" viewBox="0 0 6 12"><polyline points="0,0 5,6 0,12" fill="none" stroke="#cfd3d7"/></svg>
  <div class="feature-label">for graphic designers</div>
  <h2 class="feature-title t-magenta">GET CREATIVE !</h2>
  <div class="feature-media" role="img" aria-label="Illustration: creative head with a swoosh of colour" style="width:224px;background:linear-gradient(90deg,#8a2f8f 0%,#b3307a 25%,#e6486a 55%,#fbd0d8 85%,#fff 100%)"></div>
  <p class="feature-copy">47Vora is looking for top creative talent to deliver graphic design solutions for some leading global brands Do you have what it takes?</p>
  <div class="btn">Learn More</div>
</section>

<section class="feature abs" style="left:399px">
  <svg class="feature-arrow" width="6" height="12" viewBox="0 0 6 12"><polyline points="0,0 5,6 0,12" fill="none" stroke="#cfd3d7"/></svg>
  <div class="feature-label">for clients</div>
  <h2 class="feature-title t-orange">THE 47VORA DIFFERENCE</h2>
  <div class="feature-media" role="img" aria-label="Illustration: figure stepping ahead of a crowd" style="background:linear-gradient(135deg,#d8d8d8,#a9a9a9 70%,#e0a040)"></div>
  <p class="feature-copy">Smart, Flexible, Thoughtful: find out why leading corporations and government agencies are turning to 47Vora to help manage their most demanding IT services challenges.</p>
  <div class="btn">Learn More</div>
</section>

<section class="feature abs" style="left:687px">
  <svg class="feature-arrow" width="6" height="12" viewBox="0 0 6 12"><polyline points="0,0 5,6 0,12" fill="none" stroke="#cfd3d7"/></svg>
  <div class="feature-label">for partners</div>
  <h2 class="feature-title t-cyan">TEAM UP WITH THE BEST</h2>
  <div class="feature-media" role="img" aria-label="Photo: business handshake between partners" style="background:linear-gradient(90deg,#4a4f56,#c7b4a2 50%,#5a6470)"></div>
  <p class="feature-copy">When it comes to technology partnerships, our mission it so make you a success.</p>
  <div class="btn">Learn More</div>
</section>

<section class="services abs"></section>
<h3 class="svc-head abs" style="left:123px;top:994px">Creative Design Services</h3>
<ul class="svc-list abs" style="left:137px;top:1027px">
  <li>Print</li><li>Logo Design</li><li>Website Design</li><li>Illustration</li>
</ul>
<div class="svc-divider abs"></div>
<h3 class="svc-head abs" style="left:429px;top:994px">Business and Technology solutions</h3>
<ul class="svc-list abs" style="left:443px;top:1027px;width:230px">
  <li>Application Software and Web Development</li>
  <li>Business Process Re-Design (BPR)</li>
  <li>Business/Systems Analysis and Requirement Documentation</li>
  <li>Mentoring and Training</li>
</ul>
<ul class="svc-list abs" style="left:693px;top:1027px">
  <li>Network/Hardware Installation Services</li>
  <li>System Design and Architecture</li>
  <li>Vendor Management</li>
  <li>Docuvault Architecture and Implementation</li>
</ul>

<footer class="copyright abs">Copyright 2010, 47Vora, LLC All rights reserved.</footer>

</body>
</html>
```